Bonus/Contractor Pack Sticker

Need a sticker for a current promotion we are running. We are a Building Material company which needs a sticker to apply to existing packaging. We would like the design to be visible from a distance and to have the colour Red.

The sticker will be 6" wide by 4" tall and shall be split in the middle to be wrapped around the corner of the box. (as shown in the example)

Words which need to be included on the sticker are
"Bonus 100pcs Lifetime Durable Wedges Inside"

Target Market(s)

Contractors?Do-it Yourselfers

Industry/Entity Type

Construction

Colors
ec1f27

Requirements
Must have
• Red

```html
<!DOCTYPE html>
<html lang="en">
<head>
<meta charset="utf-8">
<title>Bonus Wedges Sticker</title>
<link rel="stylesheet" href="https://fonts.googleapis.com/css2?family=Nunito:wght@900&display=swap">
<style>
  :root {
    --sticker-red: #ec1f27;
    --ribbon-dark: #b5141b;
    --ribbon-light: #f0464c;
    --ink: #2b2b2b;
    --paper: #ffffff;
    --frame: #555555;
  }
  html, body {
    margin: 0;
    padding: 0;
    width: 1200px;
    height: 879px;
    overflow: hidden;
    background: var(--paper);
  }
  .sticker {
    position: relative;
    width: 1200px;
    height: 879px;
    font-family: "Nunito", "Arial Rounded MT Bold", sans-serif;
  }
  .sticker-art {
    position: absolute;
    inset: 0;
  }
  .sticker-text {
    position: absolute;
    left: 0;
    top: 0;
    width: 1200px;
    height: 879px;
  }
  .headline {
    font-size: 190px;
    font-weight: 900;
    letter-spacing: -2px;
  }
  .headline-shadow { fill: #111; }
  .headline-face { fill: var(--sticker-red); }
  .offer-line {
    font-size: 74px;
    font-weight: 900;
    fill: var(--ink);
    stroke: var(--paper);
    stroke-width: 10px;
    paint-order: stroke fill;
    stroke-linejoin: round;
  }
</style>
</head>
<body>
<main class="sticker">
  <svg class="sticker-art" viewBox="0 0 1200 879" width="1200" height="879">
    <defs>
      <linearGradient id="bowTone" x1="0" y1="0" x2="1" y2="1">
        <stop offset="0" stop-color="var(--ribbon-light)"/>
        <stop offset="0.5" stop-color="var(--sticker-red)"/>
        <stop offset="1" stop-color="var(--ribbon-dark)"/>
      </linearGradient>
    </defs>
    <rect class="sticker-frame" x="51" y="109" width="1100" height="731" fill="none" stroke="var(--frame)" stroke-width="2"/>
    <path class="ribbon-band" d="M51 145 C250 170 420 260 560 380 L560 440 C420 330 250 240 51 215 Z" fill="var(--sticker-red)"/>
    <path class="ribbon-band" d="M640 380 C820 520 980 630 1151 660 L1151 760 C970 730 800 630 640 470 Z" fill="var(--ribbon-dark)"/>
    <rect class="gift-bow" role="img" aria-label="Red gift bow illustration" x="286" y="300" width="610" height="420" rx="150" fill="url(#bowTone)"/>
  </svg>
  <svg class="sticker-text" viewBox="0 0 1200 879" width="1200" height="879">
    <text class="headline headline-shadow" x="578" y="332" text-anchor="middle">Bonus</text>
    <text class="headline headline-face" x="592" y="320" text-anchor="middle">Bonus</text>
    <text class="offer-line" x="590" y="428" text-anchor="middle">100 pcs</text>
    <text class="offer-line" x="590" y="513" text-anchor="middle">Lifetime</text>
    <text class="offer-line" x="590" y="600" text-anchor="middle">Durable Wedges</text>
    <text class="offer-line" x="590" y="688" text-anchor="middle">Inside</text>
  </svg>
</main>
</body>
</html>
```